Career Development Skills | Business Card & Logo Design

We are looking for a business card including logo design for a new Sydney based business called 'Bright Pathwork'.
We offer a range of services that focus on building the Employability or Employment skills for individuals focusing on job seekers and those interested in building skills required to develop their career. Employability skills are required not only to gain employment, but also to progress within an organisation so as to achieve one's potential.
Updates
Target Market(s)
Our client targets include corporates and govt agencies looking to build skills within their current employee base or assist staff in the transition between roles or workplaces.
Industry/Entity Type
Business
Look and feel
Each slider illustrates characteristics of the customer's brand and the style your logo design should communicate.

```html
<!DOCTYPE html>
<html lang="en">
<head>
<meta charset="utf-8">
<title>Bright Pathwork — Business Card</title>
<link rel="stylesheet" href="https://fonts.googleapis.com/css2?family=Cinzel:wght@700&family=Roboto+Slab:wght@700;800&display=swap">
<style>
  :root {
    --page: #161616;
    --card-dark: #1b1b1b;
    --card-mid: #2c2c2c;
    --lime: #a6d129;
    --orange: #f39a1e;
    --white: #f2f2f2;
    --rule: #a0a0a0;
    --dot: rgba(255,255,255,0.08);
  }
  * { box-sizing: border-box; margin: 0; padding: 0; }
  html, body { width: 1200px; height: 1164px; overflow: hidden; }
  body {
    background: var(--page);
    position: relative;
    font-family: "Roboto Slab", "Rockwell", serif;
    font-weight: 800;
  }

  .card {
    position: absolute;
    width: 728px;
    height: 448px;
    overflow: hidden;
    background:
      linear-gradient(200deg, rgba(255,255,255,0.16) 0%, rgba(255,255,255,0.04) 30%, rgba(255,255,255,0) 45%),
      linear-gradient(160deg, var(--card-dark) 0%, var(--card-mid) 55%, var(--card-dark) 100%);
  }
  .card--front { left: 45px; top: 88px; }
  .card--back  { left: 423px; top: 571px; }

  .ornament { position: absolute; }
  .ornament--front-left {
    left: 0; top: 0; width: 270px; height: 448px;
    background:
      radial-gradient(ellipse at 20% 85%, rgba(166,209,41,0.35), rgba(166,209,41,0) 60%),
      radial-gradient(ellipse at 75% 18%, rgba(243,154,30,0.32), rgba(243,154,30,0) 55%),
      radial-gradient(ellipse at 30% 45%, rgba(120,120,120,0.18), rgba(120,120,120,0) 60%);
  }
  .ornament--back-right {
    right: 0; top: 0; width: 300px; height: 448px;
    background: radial-gradient(ellipse at 60% 55%, rgba(130,130,130,0.22), rgba(130,130,130,0) 65%);
  }
  .ornament--back-left {
    left: 0; top: 0; width: 330px; height: 115px;
    background: radial-gradient(ellipse at 40% 40%, rgba(110,110,110,0.18), rgba(110,110,110,0) 70%);
  }
  .ornament--back-bottom {
    left: 0; bottom: 0; width: 420px; height: 90px;
    background: radial-gradient(ellipse at 30% 80%, rgba(110,110,110,0.15), rgba(110,110,110,0) 70%);
  }

  .brand-mark {
    position: absolute;
    display: flex;
    align-items: center;
    gap: 8px;
    font-family: "Roboto Slab", serif;
    font-weight: 800;
    font-size: 12px;
    letter-spacing: 1px;
    text-transform: uppercase;
    color: var(--lime);
  }
  .brand-mark__square { width: 18px; height: 18px; background: var(--orange); }
  .card--front .brand-mark { left: 10px; top: 28px; }
  .card--back .brand-mark { right: 14px; top: 32px; }

  .rule {
    position: absolute;
    height: 2px;
    background: linear-gradient(90deg, rgba(160,160,160,0), var(--rule) 12%, var(--rule) 88%, rgba(160,160,160,0));
  }
  .dot-field {
    position: absolute;
    background-image: radial-gradient(circle, var(--dot) 1.6px, transparent 2px);
    background-size: 7px 7px;
  }

  /* front title block */
  .title-block .rule--top { left: 288px; top: 194px; width: 440px; }
  .title-block .dot-field { left: 298px; top: 200px; width: 430px; height: 78px; }
  .title-block .rule--mid { left: 288px; top: 282px; width: 440px; }
  .title-block .rule--low { left: 366px; top: 324px; width: 310px; }

  .company-name {
    position: absolute;
    left: 298px; top: 218px; width: 430px;
    font-family: "Cinzel", serif;
    font-weight: 700;
    font-size: 32px;
    line-height: 40px;
    letter-spacing: 1px;
    color: var(--lime);
    text-align: center;
    white-space: nowrap;
  }
  .person {
    position: absolute;
    left: 366px; top: 294px; width: 310px;
    text-align: center;
    font-weight: 800;
    font-size: 15px;
    line-height: 22px;
    letter-spacing: 1px;
    text-transform: uppercase;
    white-space: nowrap;
  }
  .person__role { color: var(--orange); margin-right: 8px; }
  .person__name { color: var(--lime); }

  /* back contact block */
  .contact-block .rule--top { left: 0; top: 124px; width: 352px; }
  .contact-block .dot-field { left: 0; top: 130px; width: 352px; height: 215px; }
  .contact-block .rule--bottom { left: 0; top: 350px; width: 352px; }

  .contact {
    position: absolute;
    left: 40px; top: 135px;
    font-weight: 800;
    font-size: 16px;
    line-height: 22px;
    letter-spacing: 0.8px;
    white-space: nowrap;
  }
  .contact__address { color: var(--lime); font-style: normal; }
  .contact__lines { margin-top: 10px; color: var(--white); }
  .contact__lines dt { display: inline-block; width: 62px; }
  .contact__lines dd { display: inline; }
  .contact__lines dd::after { content: ""; display: block; height: 2px; }
  .contact__web { margin-top: 6px; color: var(--orange); }
</style>
</head>
<body>

  <section class="card card--front" aria-label="Business card front">
    <div class="ornament ornament--front-left" role="img" aria-label="Orange, lime and grey flourish scrollwork"></div>
    <div class="brand-mark"><span class="brand-mark__square"></span><span>Bright Pathwork</span></div>
    <div class="title-block">
      <div class="dot-field"></div>
      <div class="rule rule--top"></div>
      <h1 class="company-name">BRIGHT PATHWORK</h1>
      <div class="rule rule--mid"></div>
      <p class="person"><span class="person__role">Director</span><span class="person__name">Daniel Horne</span></p>
      <div class="rule rule--low"></div>
    </div>
  </section>

  <section class="card card--back" aria-label="Business card back">
    <div class="ornament ornament--back-left" role="img" aria-label="Faint grey flourish scrollwork"></div>
    <div class="ornament ornament--back-right" role="img" aria-label="Faint grey flourish scrollwork"></div>
    <div class="ornament ornament--back-bottom" role="img" aria-label="Faint grey flourish scrollwork"></div>
    <div class="brand-mark"><span class="brand-mark__square"></span><span>Bright Pathwork</span></div>
    <div class="contact-block">
      <div class="dot-field"></div>
      <div class="rule rule--top"></div>
      <div class="contact">
        <address class="contact__address">
          Level 14<br>
          Harbour Court Tower 3<br>
          88 Kent Lane<br>
          Harbour Court, Sydney 2000
        </address>
        <dl class="contact__lines">
          <dt>Tel</dt><dd>(02)&nbsp;&nbsp;55501840</dd>
          <dt>Fax</dt><dd>(02)&nbsp;&nbsp;55501870</dd>
        </dl>
        <div class="contact__web">
          brightpathwork.com.au<br>
          daniel@brightpathwork.com.au
        </div>
      </div>
      <div class="rule rule--bottom"></div>
    </div>
  </section>

</body>
</html>
```